Storm Restoration Contractor needs a professional letterhead design

Looking for a professional letterhead design. Not looking for your cheapo MS Word standard ones that are readily available. Dont want it to be cookie cutter look like ones readily available online. We just recently changed our logo and want to freshen up all our documents. Our company handles restoring a property back to a pre-loss condition after a storm damages it. For example, wind, hail, flood, fire losses.

Target Market(s)

Property Owners, Homeowners, Property Owners, Commercial Property Owners, Property Management Companies

Industry/Entity Type

Construction Company

Requirements
Must have
• Professional, Use 1 of 2 logo options
• Storm Restoration, Roofing, Siding, Windows

```html
<!DOCTYPE html>
<html lang="en">
<head>
<meta charset="utf-8">
<title>Stormline Exteriors Letterhead</title>
<link rel="stylesheet" href="https://fonts.googleapis.com/css2?family=Questrial&family=Mulish:wght@700&display=swap">
<style>
  :root {
    --backdrop: #bdbdbd;
    --paper: #f1f1f1;
    --brand-blue: #2468b0;
    --brand-gray: #555555;
    --ink: #333333;
    --ink-soft: #4a4a4a;
    --rule-gray: #9a9a9a;
  }
  * { margin: 0; padding: 0; box-sizing: border-box; }
  html, body {
    width: 1200px; height: 1041px; overflow: hidden;
    background: var(--backdrop);
  }
  .letterhead {
    position: absolute; left: 280px; top: 106px;
    width: 640px; height: 826px;
    background: var(--paper);
    font-family: "Questrial", sans-serif;
    color: var(--ink);
    overflow: hidden;
  }
  .brand { position: absolute; left: 51px; top: 42px; display: flex; align-items: center; }
  .brand-mark {
    width: 46px; height: 46px; border-radius: 50%;
    border: 5px solid var(--brand-blue);
  }
  .brand-divider { width: 2px; height: 50px; background: var(--brand-blue); margin: 0 6px 0 8px; }
  .brand-name {
    color: var(--brand-blue); font-weight: 400;
    font-size: 20px; line-height: 19px; letter-spacing: 1.2px; text-transform: uppercase;
  }
  .contact { position: absolute; left: 463px; font-size: 8.4px; color: var(--ink-soft); }
  .contact-address { top: 39px; border-left: 2px solid var(--brand-blue); padding-left: 9px; line-height: 11.2px; }
  .contact-lines { top: 71px; border-left: 1px solid var(--rule-gray); padding-left: 11px; line-height: 11.2px; height: 34px; }
  .contact-line { display: flex; align-items: center; gap: 6px; }
  .contact-line svg { width: 7px; height: 7px; fill: var(--brand-blue); }
  .letter { position: absolute; left: 51px; width: 538px; font-size: 9.3px; line-height: 11.2px; }
  .date { top: 181px; }
  .recipient { top: 204px; font-style: normal; }
  .salutation { top: 298px; font-family: "Mulish", sans-serif; font-weight: 700; }
  .body { top: 322px; text-align: justify; }
  .body p { margin-bottom: 11.2px; }
  .closing { top: 558px; }
  .closing .signer { font-family: "Mulish", sans-serif; font-weight: 700; }
  .signature-area {
    position: absolute; left: 124px; top: 544px; width: 136px; height: 68px;
    background: linear-gradient(135deg, rgba(36,104,176,0.08), rgba(36,104,176,0.16));
    border-radius: 3px;
  }
  .footer-band {
    position: absolute; left: 0; bottom: 0; width: 640px; height: 40px;
    background: linear-gradient(90deg, var(--brand-gray) 0%, var(--brand-gray) 55%, var(--brand-blue) 100%);
  }
</style>
</head>
<body>
<main class="letterhead">
  <header>
    <div class="brand">
      <div class="brand-mark"></div>
      <div class="brand-divider"></div>
      <div class="brand-name">Stormline<br>Exteriors</div>
    </div>
    <div class="contact contact-address">
      4120 N Canyon Ridge Road STE 210<br>Mesa, AZ 85201
    </div>
    <div class="contact contact-lines">
      <div class="contact-line">
        <svg viewBox="0 0 10 10"><path d="M2 0.5 L3.6 2.6 L2.7 3.7 Q4 6.2 6.3 7.3 L7.4 6.4 L9.5 8 L8.3 9.6 Q4.5 9.5 1.9 6.5 Q0 4 0.5 1.6 Z"/></svg>480-555-0142
      </div>
      <div class="contact-line">
        <svg viewBox="0 0 10 10"><rect x="2.5" y="0.5" width="5" height="3"/><rect x="0.5" y="3.8" width="9" height="3.8" rx="0.6"/><rect x="2.5" y="7" width="5" height="2.5"/></svg>480-555-0143
      </div>
      <div class="contact-line">
        <svg viewBox="0 0 10 10"><path d="M0.5 2 H9.5 V8.5 H0.5 Z M1.2 2.6 L5 5.6 L8.8 2.6" fill="none" stroke="#2468b0" stroke-width="1.2"/></svg>info@stormlineext.com
      </div>
    </div>
  </header>

  <div class="letter date">30.11.2016</div>
  <address class="letter recipient">
    Recipient's name<br>Lindenweg 4<br>10115 Berlin<br>Germany
  </address>
  <div class="letter salutation">Dear sir,</div>
  <div class="letter body">
    <p>Communication is a very integral part of living creatures, animals and humans. Communication may be verbal or written. Written communication however is only applicable to human beings. Can you even imagine a world without communication? Verbal communication can be through telephones, webcams or in person. Written communication is through letters, emails and mobile phone messages.</p>
    <p>In today's world of great inventions and technology, letters have somehow become redundant. It is the time for text messages or chats. But they still can communicate a lot more than all other modes of communication. Organizations and various government departments still bank on letters as a strong medium of communication. There is no comparison in costs of sending letters as compared to costs of mobile phone messages though – letters are far cheaper. Letters now commonly known as “hard copy documents” are considered more relevant and important than email copies of text messages as proof or evidence of some sort.</p>
    <p>Letters speak volumes about a person or an organization that writes it. So one must take utmost care ensuring that the language used in any letter is appropriate for the occasion for which it is being written. Since a letter is also a written proof or document, if there are certain things that should not form a part of it, then that too should be carefully handled.</p>
    <p>Writing a good letter is an art. But if for some reason someone is unable to write that perfect letter, these different types of letters provide a base for you to build on. Sample letters have been given for everyone to understand what all information needs to form a part of the letter type and then it can be customized.</p>
  </div>
  <div class="letter closing">Yours Sincerely,<br><span class="signer">Dana Whitfield</span></div>
  <div class="signature-area" role="img" aria-label="Handwritten signature in blue ink"></div>

  <div class="footer-band" role="img" aria-label="Decorative gray and blue footer wave"></div>
</main>
</body>
</html>
```